KELBRIDGE PAINTING

We are a painting company. We paint residential, commercial and strata jobs. I need the website to be very sharp, neat and elegant. I've attached our logo. the Logo needs to be embossed as a gold color and the background like a Matt black. I need these tabs:

• HOME • ABOUT US • SERVICES • TESTIMONIALS • SHOWCASE • CONTACT US

Be creative and innovative in your style.
take this as an example to just get the gist of what I'm expecting. If you can better it then the job is yours!

http://rickhalvorpainting.com.au/contact.html

I look forward to seeing your artwork :)

#These are the links to my logo in PSD format.

https://www.filevaultzy.com/s/qwertplk83nd7ha/Kelbridge%20Painting%20Luxury%20Gold.rar

https://www.filevaultzy.com/sh/bzuyrak2m5wqp9/QoPL7-xvMn

Painting

• Making the Logo embossed like the artworks i have attached is definitely a necessity.

Can you let me know if this is possible to apply to the website.

thank you

```html
<!DOCTYPE html>
<html lang="en">
<head>
<meta charset="utf-8">
<title>Kelbridge Painting – Contact Us</title>
<link rel="stylesheet" href="https://fonts.googleapis.com/css2?family=Lato:wght@300;400;700&family=Montserrat:wght@700&display=swap">
<style>
  :root {
    --matt-black: #222222;
    --header-black: #232323;
    --paint-red: #ec2b43;
    --paint-red-soft: #e42a3a;
    --gold: #d4a017;
    --white: #ffffff;
    --navy: #0d3550;
    --rule: #9a9a9a;
  }
  * { box-sizing: border-box; margin: 0; padding: 0; }
  html, body { width: 1200px; height: 1000px; overflow: hidden; }
  body { position: relative; background: var(--matt-black); font-family: "Lato", sans-serif; color: var(--white); }

  .site-header { position: absolute; left: 0; top: 0; width: 1200px; height: 70px; background: var(--header-black); }
  .brand { position: absolute; left: 241px; top: 18px; display: flex; align-items: center; }
  .brand-mark { width: 42px; height: 42px; border-radius: 50%; border: 2px solid var(--gold); }
  .brand-text { margin-left: 5px; margin-top: -6px; }
  .brand-name { font-family: "Lato", sans-serif; font-weight: 700; font-size: 14px; color: var(--white); letter-spacing: 0.1px; line-height: 1; }
  .brand-tagline { font-size: 7.5px; font-weight: 700; margin-left: 25px; margin-top: 2px; }

  .main-nav { position: absolute; top: 34px; right: 212px; display: flex; gap: 24px; }
  .main-nav a { color: var(--white); text-decoration: none; font-family: Arial, Helvetica, sans-serif; font-weight: 700; font-size: 9.5px; letter-spacing: 0.1px; position: relative; }
  .main-nav a.is-active::before { content: ""; position: absolute; left: 4px; top: -34px; width: 57px; height: 4px; background: var(--gold); }

  .spectrum-band { position: absolute; left: 0; top: 68px; width: 1200px; height: 6px;
    background: linear-gradient(90deg, #d01020 0%, #7a1a8a 20%, #2040c0 35%, #20b0c0 50%, #30c030 65%, #f0d020 80%, #e03020 100%); }

  .contact-section { position: absolute; left: 0; top: 74px; width: 1200px; height: 636px; background: var(--paint-red); }
  .hero-image-area { position: absolute; left: 247px; top: 80px; width: 325px; height: 556px;
    background: linear-gradient(180deg, var(--paint-red) 0%, var(--paint-red-soft) 100%); }
  .section-title { position: absolute; top: 22px; left: 0; width: 1230px; text-align: center; font-family: "Montserrat", sans-serif; font-weight: 700; font-size: 19px; letter-spacing: 1px; }
  .section-intro { position: absolute; top: 67px; left: 0; width: 1230px; text-align: center; font-weight: 300; font-size: 16px; line-height: 18px; letter-spacing: 0.5px; }

  .quote-form { position: absolute; left: 368px; top: 124px; width: 496px; }
  .quote-form h2 { font-weight: 400; font-size: 15.5px; letter-spacing: 0.4px; margin-left: 1px; }
  .field { position: absolute; left: 0; width: 496px; }
  .field label { display: block; font-size: 11.5px; letter-spacing: 0.3px; line-height: 14px; height: 18px; }
  .field input, .field textarea { display: block; width: 496px; height: 27px; border: 0; background: var(--white); }
  .field textarea { height: 110px; resize: none; }
  .form-actions { position: absolute; left: 0; top: 425px; display: flex; gap: 8px; }
  .form-actions button { width: 107px; height: 33px; border: 0; background: var(--navy); color: var(--white); font-family: "Lato", sans-serif; font-size: 12px; letter-spacing: 0.5px; }

  .site-footer { position: absolute; left: 0; top: 710px; width: 1200px; height: 290px; background: var(--matt-black); text-align: center; }
  .footer-title { position: absolute; top: 41px; left: 0; width: 1230px; font-family: "Montserrat", sans-serif; font-weight: 700; font-size: 18px; letter-spacing: 1.6px; }
  .footer-details { position: absolute; top: 92px; left: 0; width: 1228px; font-size: 19.5px; line-height: 23px; letter-spacing: 0.6px; }
  .footer-rule { position: absolute; left: 239px; top: 218px; width: 749px; height: 1px; background: var(--rule); }
  .copyright { position: absolute; top: 245px; left: 0; width: 1228px; font-size: 19.5px; letter-spacing: 0.4px; }
</style>
</head>
<body>
  <header class="site-header">
    <div class="brand">
      <span class="brand-mark"></span>
      <div class="brand-text">
        <div class="brand-name">KELBRIDGE PAINTING</div>
        <div class="brand-tagline">Painting Australia Everyday!</div>
      </div>
    </div>
    <nav class="main-nav">
      <a href="#">HOME</a>
      <a href="#">ABOUT US</a>
      <a href="#">SERVICES</a>
      <a href="#">TESTIMONIALS</a>
      <a href="#">SHOWCASE</a>
      <a href="#" class="is-active">CONTACT US</a>
    </nav>
  </header>
  <div class="spectrum-band"></div>

  <section class="contact-section">
    <div class="hero-image-area" role="img" aria-label="Photo of a tipped paint can pouring red paint"></div>
    <h1 class="section-title">CONTACT US</h1>
    <p class="section-intro">To enjoy our services for your comfortable living… Just give a call.<br>Your comfort is our utmost priority and we promise the best for you</p>

    <form class="quote-form">
      <h2>FOR A FREE QUOTE CONTACT US NOW</h2>
      <div class="field" style="top:32px"><label>NAME*</label><input type="text"></div>
      <div class="field" style="top:94px"><label>EMAIL*</label><input type="email"></div>
      <div class="field" style="top:158px"><label>PHONE*</label><input type="tel"></div>
      <div class="field" style="top:223px"><label>&nbsp;ADDRESS*</label><input type="text"></div>
      <div class="field" style="top:287px"><label>COMMENT*</label><textarea></textarea></div>
      <div class="form-actions">
        <button type="submit">SUMIT</button>
        <button type="reset">RESET</button>
      </div>
    </form>
  </section>

  <footer class="site-footer">
    <h2 class="footer-title">STAY IN TOUCH WITH US</h2>
    <p class="footer-details">
      CONTACT NAME : DANIEL MARSH<br>
      SERVICING AREAS : HARLOW VALE, WESTERN AUSTRALIA<br>
      PHONE : 0198 752 340&nbsp; MOBILE : 0198 752 341<br>
      REG NO : 1234&nbsp; EMAIL : KELBRIDGE@MAILVARRA.COM.AU
    </p>
    <div class="footer-rule"></div>
    <p class="copyright">copyright©2013 Kelbridge Painting</p>
  </footer>
</body>
</html>
```